sydney wedding photography business needs a business card design

we need a business card design for a sydney based wedding photography and videography business. our business name is :golden hour studio and film. our target clients are 24-35 yrs female. our style is candid, organic, natural, dynamic. we are a team of young photographers and videographers, and help brides to create memories that they will cherish for the rest of their lives. the logo will be provided. we want an elegant design that reflects our style, and also want to give a great impression to our clients that we are one of the best studios in sydney and our brand means quality and premium service.

Target Market(s)

bride to be, 24-35 years old, living in sydney and surrunding areas

Industry/Entity Type

Wedding Photography

Contact Information for Business Card

address: 57 tarrant street, glenmore nsw 2047
mobile: 0431872259
phone: (02) 9163 2408
info@tidewillowstudio.net.au
www.tidewillowstudio.net.au
facebook:tidewillowweddings
instagram:tidewillowweddings

Font styles to use
Serif
Sans Serif

Requirements
Nice to have
• maybe add my slogan"memories beyond eternity" if the layout looks good
Should not have
• no black color, not good idea for wedding biz card

```html
<!DOCTYPE html>
<html lang="en">
<head>
<meta charset="utf-8">
<title>Golden Hour Studio and Film – Business Card</title>
<link rel="stylesheet" href="https://fonts.googleapis.com/css2?family=Montserrat:wght@400;500;600&display=swap">
<style>
  :root {
    --bg: #2e2e30;
    --gold-light: #f0c23a;
    --gold: #d9a21b;
    --gold-deep: #b9800c;
    --ink: #2a1f12;
    --bronze-light: #6a4c2a;
    --bronze: #553c21;
    --bronze-deep: #45301a;
    --text-light: #f4ead8;
    --text-gold: #f2c24a;
  }
  * { box-sizing: border-box; margin: 0; padding: 0; }
  html, body { width: 1200px; height: 843px; overflow: hidden; }
  body {
    background: var(--bg);
    font-family: "Montserrat", Arial, sans-serif;
    position: relative;
  }
  .card {
    position: absolute;
    width: 540px;
    height: 309px;
    top: 267px;
    border-radius: 4px;
    overflow: hidden;
    box-shadow: 0 12px 30px rgba(0,0,0,.45);
  }
  /* Gold side */
  .card--back {
    left: 40px;
    background: linear-gradient(135deg, var(--gold-light) 0%, var(--gold) 50%, var(--gold-deep) 100%);
  }
  .card--back .brand-name {
    position: absolute;
    left: 0; right: 0; top: 118px;
    text-align: center;
    font-weight: 600;
    font-size: 30px;
    letter-spacing: .5px;
    color: var(--ink);
  }
  .card--back .divider {
    position: absolute;
    left: 170px; right: 170px; top: 196px;
    height: 1px;
    background: rgba(42,31,18,.45);
  }
  .card--back .social {
    position: absolute;
    left: 0; right: 0; top: 210px;
    text-align: center;
    font-size: 12px;
    color: var(--ink);
  }
  /* Bronze side */
  .card--front {
    left: 620px;
    background: linear-gradient(160deg, var(--bronze-light) 0%, var(--bronze) 50%, var(--bronze-deep) 100%);
  }
  .facets {
    position: absolute;
    right: 0; top: 0;
    width: 230px; height: 309px;
    background: linear-gradient(200deg, rgba(217,162,27,.28) 0%, rgba(217,162,27,.12) 55%, rgba(217,162,27,0) 100%);
  }
  .contact-list {
    position: absolute;
    left: 34px; top: 32px;
    list-style: none;
    font-size: 13px;
    color: var(--text-light);
    line-height: 19px;
  }
  .contact-list li { display: flex; align-items: center; gap: 8px; }
  .contact-list svg { width: 12px; height: 12px; fill: var(--text-gold); flex: none; }
  .card--front .brand-name {
    position: absolute;
    left: 34px; top: 120px;
    font-weight: 600;
    font-size: 28px;
    color: var(--text-gold);
    letter-spacing: .5px;
  }
  .address {
    position: absolute;
    left: 34px; top: 208px;
    font-size: 13px;
    font-style: normal;
    line-height: 19px;
    color: var(--text-light);
  }
  .person {
    position: absolute;
    right: 46px; top: 214px;
    text-align: center;
  }
  .person-name { font-size: 17px; font-weight: 600; color: var(--text-gold); }
  .person-title { font-size: 14px; color: var(--text-light); margin-top: 2px; }
</style>
</head>
<body>
  <section class="card card--back">
    <div class="brand-name">golden hour studio and film</div>
    <div class="divider"></div>
    <div class="social">tidewillowweddings</div>
  </section>

  <section class="card card--front">
    <div class="facets" role="img" aria-label="Faceted soft gold geometric decoration"></div>
    <ul class="contact-list">
      <li>
        <svg viewBox="0 0 12 12" aria-hidden="true"><path d="M2 1h2.5l1 2.5-1.3 1a6 6 0 0 0 3.3 3.3l1-1.3L11 7.5V10a1 1 0 0 1-1 1A9 9 0 0 1 1 2a1 1 0 0 1 1-1z"/></svg>
        (02) 9163 2408
      </li>
      <li>
        <svg viewBox="0 0 12 12" aria-hidden="true"><path d="M3.5 0h5a1 1 0 0 1 1 1v10a1 1 0 0 1-1 1h-5a1 1 0 0 1-1-1V1a1 1 0 0 1 1-1zm.5 1.5v7.5h4V1.5zM6 9.8a.7.7 0 1 0 0 1.4.7.7 0 0 0 0-1.4z"/></svg>
        (04) 3187 2259
      </li>
      <li>
        <svg viewBox="0 0 12 12" aria-hidden="true"><path d="M0 2.5h12v7H0zm1 .8v.3l5 3 5-3v-.3z"/></svg>
        info@tidewillowstudio.net.au
      </li>
    </ul>
    <div class="brand-name">golden hour studio and film</div>
    <address class="address">
      57 tarrant street<br>
      glenmore nsw 2047<br>
      www.tidewillowstudio.net.au
    </address>
    <div class="person">
      <div class="person-name">Mara Ellison</div>
      <div class="person-title">President</div>
    </div>
  </section>
</body>
</html>
```